Business Card Design

New business card design

Target Market(s)

Residential & Commercial Property Managers

Industry/Entity Type

Plumbing Services

Contact Information for Business Card

Name - Rowan Keddle, title - Director, Phone Number - 0431 286 517, email - rowan@tbk-plumbing.com.au, Company ABN - 73 215 904 386,

Font styles to use
Sans Serif

Colors
0054AA
0677BA
7BADD7
CADEEF
E8F1F8

```html
<!DOCTYPE html>
<html lang="en">
<head>
<meta charset="utf-8">
<title>TBK Plumbing Services – Business Card</title>
<link rel="stylesheet" href="https://fonts.googleapis.com/css2?family=Roboto:wght@300;400;700&display=swap">
<style>
  :root {
    --blue-deep: #0054AA;
    --blue-mid: #0677BA;
    --blue-soft: #7BADD7;
    --blue-pale: #CADEEF;
    --blue-mist: #E8F1F8;
    --navy: #0a3f82;
    --ink: #1c1c1c;
    --paper: #ffffff;
    --backdrop: #2a2a2c;
  }
  * { box-sizing: border-box; margin: 0; padding: 0; }
  html, body { width: 1200px; height: 852px; overflow: hidden; }
  body {
    background: var(--backdrop);
    font-family: "Roboto", Arial, sans-serif;
    position: relative;
  }
  .card {
    position: absolute;
    top: 267px;
    width: 520px;
    height: 318px;
    border-radius: 22px;
    overflow: hidden;
  }
  .card-front { left: 50px; background: var(--blue-mid); }
  .card-back { left: 630px; background: var(--paper); }
  .card-art { position: absolute; inset: 0; width: 100%; height: 100%; }

  .front-fill {
    position: absolute;
    inset: 0;
    background: linear-gradient(170deg, #3aa6d6 0%, var(--blue-mid) 45%, var(--blue-deep) 100%);
  }

  .brand {
    position: absolute;
    left: 0; right: 0;
    text-align: center;
    font-weight: 300;
    letter-spacing: 0.04em;
    white-space: nowrap;
  }
  .brand-front { top: 128px; font-size: 40px; color: var(--paper); }
  .brand-back { top: 38px; font-size: 34px; color: var(--ink); }
  .brand-dot {
    display: inline-block;
    width: 10px; height: 10px;
    border-radius: 50%;
    background: var(--blue-soft);
    margin-right: 12px;
    vertical-align: middle;
  }

  .contact-band {
    position: absolute;
    left: 0; right: 0;
    top: 118px;
    height: 126px;
    background: linear-gradient(90deg, var(--blue-deep), var(--blue-mid));
  }

  .person {
    position: absolute;
    top: 152px;
    right: 268px;
    text-align: right;
    color: var(--paper);
  }
  .person-name { font-size: 20px; font-weight: 700; line-height: 1.2; }
  .person-title { font-size: 13px; font-weight: 300; color: var(--blue-pale); margin-top: 2px; }
  .person-abn { font-size: 13px; font-weight: 300; color: var(--blue-pale); margin-top: 8px; }

  .divider {
    position: absolute;
    left: 268px;
    top: 140px;
    width: 1px;
    height: 88px;
    background: var(--blue-soft);
    opacity: 0.7;
  }

  .contacts {
    position: absolute;
    left: 286px;
    top: 146px;
    list-style: none;
    color: var(--paper);
    font-size: 12.5px;
    font-weight: 300;
  }
  .contacts li { display: flex; align-items: center; gap: 9px; height: 21px; }
  .contacts svg { width: 12px; height: 12px; fill: var(--paper); flex: none; }

  .location {
    position: absolute;
    right: 28px;
    bottom: 30px;
    font-size: 13px;
    color: var(--ink);
    font-weight: 400;
  }
  .location .sep { color: var(--blue-mid); margin: 0 6px; }
</style>
</head>
<body>

<section class="card card-front" aria-label="Card front">
  <div class="front-fill" role="img" aria-label="Layered blue water wave pattern"></div>
  <div class="brand brand-front"><span class="brand-dot"></span>TBK Plumbing Services</div>
</section>

<section class="card card-back" aria-label="Card back">
  <div class="contact-band"></div>
  <div class="brand brand-back"><span class="brand-dot"></span>TBK Plumbing Services</div>

  <div class="person">
    <p class="person-name">Rowan Keddle</p>
    <p class="person-title">Director</p>
    <p class="person-abn">ABN - 73 215 904 386</p>
  </div>

  <span class="divider"></span>

  <ul class="contacts">
    <li>
      <svg viewBox="0 0 24 24" aria-hidden="true"><path d="M6.6 10.8a15.1 15.1 0 0 0 6.6 6.6l2.2-2.2a1 1 0 0 1 1-.25 11.4 11.4 0 0 0 3.6.57 1 1 0 0 1 1 1V20a1 1 0 0 1-1 1A17 17 0 0 1 3 4a1 1 0 0 1 1-1h3.5a1 1 0 0 1 1 1c0 1.25.2 2.45.57 3.57a1 1 0 0 1-.25 1Z"/></svg>
      0431 286 517
    </li>
    <li>
      <svg viewBox="0 0 24 24" aria-hidden="true"><path d="M2 5h20v14H2Z M3.5 6.5 12 13l8.5-6.5" fill="none" stroke="#fff" stroke-width="2"/></svg>
      rowan@tbk-plumbing.com.au
    </li>
    <li>
      <svg viewBox="0 0 24 24" aria-hidden="true"><circle cx="12" cy="12" r="9" fill="none" stroke="#fff" stroke-width="2"/><path d="M3 12h18M12 3c3 3 3 15 0 18M12 3c-3 3-3 15 0 18" fill="none" stroke="#fff" stroke-width="1.6"/></svg>
      www.tbk-plumbing.com.au
    </li>
  </ul>

  <p class="location">Sydney<span class="sep">|</span>NSW<span class="sep">|</span>Australia</p>
</section>

</body>
</html>
```